Ward Compass Business Card Design*

We need a business card design for our company Ward Compass. Our company is specialized in providing online consulting services regarding medical institutions, hospitals and doctors. We work with patients worldwide looking to choose between healthcare providers. We have a website you may use as a reference, where we list doctors and clinics worldwide. So we target Medical providers as well as patients worldwide.
Target Market(s)
Medical Providers and patients around the world
Industry/Entity Type
Medical
Contact Information for Business Card
Salwa Kettani
CEO
+90 612 348 2175
info@wardcompass.example
www.wardcompass.example
14 Annakhil 7 H.R.B. Rabat, Morocco
Requirements
Must have
- Company logo/name on one full side, personal info and smaller logo and company name on the other side.
Nice to have
- Smart and elegant design

```html
<!DOCTYPE html>
<html lang="en">
<head>
<meta charset="utf-8">
<title>Ward Compass Business Card</title>
<link rel="stylesheet" href="https://fonts.googleapis.com/css2?family=Poppins:wght@400;500;600&display=swap">
<style>
  :root {
    --canvas: #e4e4e4;
    --paper: #ffffff;
    --navy: #123c66;
    --navy-top: #1f4e7e;
    --navy-bottom: #143a6b;
    --ink-light: #ffffff;
  }
  * { margin: 0; padding: 0; box-sizing: border-box; }
  html, body { width: 1200px; height: 1200px; overflow: hidden; }
  body {
    background: var(--canvas);
    font-family: "Poppins", sans-serif;
    position: relative;
  }
  .card {
    position: absolute;
    left: 257px;
    width: 686px;
    height: 392px;
    overflow: hidden;
  }
  .card--front { top: 165px; background: var(--paper); }
  .card--back {
    top: 653px;
    background: linear-gradient(180deg, var(--navy-top), var(--navy-bottom));
  }
  .card__panel { position: absolute; inset: 0; width: 100%; height: 100%; }

  .brand {
    position: absolute;
    display: flex;
    align-items: center;
    gap: 14px;
    font-weight: 600;
    letter-spacing: 0.5px;
    white-space: nowrap;
  }
  .brand__mark { border-radius: 50%; flex: none; }
  .brand--front { left: 38px; top: 103px; color: var(--navy); font-size: 25px; }
  .brand--front .brand__mark { width: 50px; height: 50px; border: 7px solid var(--navy); }
  .brand--back {
    left: 50%; top: 50%;
    transform: translate(-50%, -58%);
    color: var(--ink-light); font-size: 31px; gap: 18px;
  }
  .brand--back .brand__mark { width: 70px; height: 70px; border: 9px solid var(--ink-light); }

  .details {
    position: absolute;
    right: 34px;
    top: 192px;
    text-align: right;
    color: var(--ink-light);
    font-size: 15px;
    line-height: 19px;
  }
  .details__name { font-size: 26px; font-weight: 500; line-height: 30px; }
  .details__role { margin-bottom: 13px; }
  .details__address { margin-bottom: 13px; }
  .contact { display: flex; justify-content: flex-end; align-items: center; gap: 7px; }
  .contact svg { width: 12px; height: 12px; fill: var(--ink-light); flex: none; }
</style>
</head>
<body>

<section class="card card--front" aria-label="Business card front">
  <svg class="card__panel" viewBox="0 0 800 457" preserveAspectRatio="none" aria-hidden="true">
    <defs>
      <linearGradient id="navy-fill" x1="0" x2="0" y1="0" y2="1">
        <stop offset="0" stop-color="#164a74"/>
        <stop offset="1" stop-color="#0f3860"/>
      </linearGradient>
    </defs>
    <path fill="url(#navy-fill)" d="M0,350 C90,400 170,420 250,410 C390,392 500,250 620,165 C690,120 750,115 800,125 L800,457 L0,457 Z"/>
  </svg>

  <div class="brand brand--front">
    <span class="brand__mark"></span>
    <span class="brand__name">WARD COMPASS</span>
  </div>

  <div class="details">
    <p class="details__name">Salwa Kettani</p>
    <p class="details__role">CEO</p>
    <p class="details__address">14 Annakhil 7<br>H.R.B. Rabat, Morocco</p>
    <p class="contact">+90 612 348 2175
      <svg viewBox="0 0 24 24" aria-hidden="true"><path d="M6.6 10.8a15.1 15.1 0 0 0 6.6 6.6l2.2-2.2c.3-.3.7-.4 1-.2 1.1.4 2.3.6 3.6.6.6 0 1 .4 1 1V20c0 .6-.4 1-1 1C10.6 21 3 13.4 3 4c0-.6.4-1 1-1h3.5c.6 0 1 .4 1 1 0 1.3.2 2.5.6 3.6.1.3 0 .7-.2 1z"/></svg>
    </p>
    <p class="contact">info@wardcompass.example
      <svg viewBox="0 0 24 24" aria-hidden="true"><path d="M2 5h20v14H2z"/><path d="M2 5h20L12 12.5z" fill="#123c66"/></svg>
    </p>
    <p class="contact">www.wardcompass.example
      <svg viewBox="0 0 24 24" aria-hidden="true"><path d="M12 2a10 10 0 1 0 0 20 10 10 0 0 0 0-20zm0 2c.8 1.2 1.5 2.5 1.9 4h-3.8c.4-1.5 1.1-2.8 1.9-4zM4.3 14a8.2 8.2 0 0 1 0-4h3.4a16.5 16.5 0 0 0 0 4zM12 20c-.8-1.2-1.5-2.5-1.9-4h3.8c-.4 1.5-1.1 2.8-1.9 4zm2.3-6H9.7a14.7 14.7 0 0 1 0-4h4.6a14.7 14.7 0 0 1 0 4zm2 0a16.5 16.5 0 0 0 0-4h3.4a8.2 8.2 0 0 1 0 4z"/></svg>
    </p>
  </div>
</section>

<section class="card card--back" aria-label="Business card back">
  <div class="brand brand--back">
    <span class="brand__mark"></span>
    <span class="brand__name">WARD COMPASS</span>
  </div>
</section>

</body>
</html>
```